Consulting company requires a logo and business card design

I require a logo/business card design for a new company based in Sexsmith Alberta called TallMarsh Integrity Consulting Ltd. I plan to provide the following services: Construction management/inspection for the oil and gas industry, as well as general consulting for Asset Management, fleet management, etc. Have attached a copy of resume for use as guide for

Target Market(s)

Businesses within the oil and gas production, construction and shipping industry

Industry/Entity Type

Oil And Gas

Contact Information for Business Card

Believe should highlight, services offered, safety, quality,

Logo Text

TallMarsh Integrity Consulting (TMIC) ?

Font styles to use
Script

Requirements
Must have
• Open to all options

```html
<!DOCTYPE html>
<html lang="en">
<head>
<meta charset="utf-8">
<title>TallMarsh Integrity Consulting Ltd — Business Card</title>
<link rel="stylesheet" href="https://fonts.googleapis.com/css2?family=Questrial&family=Open+Sans:wght@400;700&display=swap">
<style>
  :root {
    --backdrop: #8f8f8f;
    --card-white: #ffffff;
    --brand-blue: #3f8ff0;
    --sky-top: #3f8ff0;
    --sky-bottom: #58fbfd;
    --flame-top: #e8701a;
    --flame-bottom: #c21c06;
    --ink-light: #ffffff;
    --logo-ink: #2f7fe0;
  }
  * { box-sizing: border-box; margin: 0; padding: 0; }
  html, body {
    width: 1200px;
    height: 900px;
    overflow: hidden;
  }
  body {
    background: var(--backdrop);
    position: relative;
    font-family: "Open Sans", sans-serif;
  }
  .card {
    position: absolute;
    left: 320px;
    width: 560px;
    height: 320px;
    overflow: hidden;
    box-shadow: 0 6px 18px rgba(0,0,0,0.25);
  }
  .card--front {
    top: 110px;
    background: var(--card-white);
    display: flex;
    align-items: center;
    justify-content: center;
  }
  .card--back { top: 470px; }

  .logo {
    display: flex;
    align-items: center;
    gap: 16px;
  }
  .logo__dot {
    width: 44px;
    height: 44px;
    border-radius: 50%;
    background: var(--brand-blue);
  }
  .logo__name {
    font-family: "Questrial", sans-serif;
    color: var(--logo-ink);
    font-weight: 400;
    line-height: 1.1;
  }
  .logo__primary {
    display: block;
    font-size: 44px;
    letter-spacing: 1px;
  }
  .logo__secondary {
    display: block;
    font-size: 17px;
    letter-spacing: 3px;
    margin-top: 4px;
  }

  .card__art {
    position: absolute;
    inset: 0;
    width: 560px;
    height: 320px;
  }
  .contact {
    position: absolute;
    right: 30px;
    top: 46px;
    text-align: right;
    color: var(--ink-light);
  }
  .contact__name {
    font-weight: 700;
    font-size: 19px;
    line-height: 1.2;
  }
  .contact__title {
    font-size: 15px;
    margin-bottom: 26px;
  }
  .contact__row {
    display: flex;
    justify-content: flex-end;
    align-items: center;
    gap: 8px;
    font-size: 15px;
    line-height: 21px;
  }
  .contact__row--address { margin-top: 12px; }
  .contact__icon {
    width: 12px;
    height: 12px;
    flex: none;
  }
  .contact__icon--blank { visibility: hidden; }
</style>
</head>
<body>

  <section class="card card--front">
    <div class="logo">
      <span class="logo__dot"></span>
      <span class="logo__name">
        <span class="logo__primary">TallMarsh</span>
        <span class="logo__secondary">Integrity Consulting Ltd</span>
      </span>
    </div>
  </section>

  <section class="card card--back">
    <svg class="card__art" viewBox="0 0 560 320" aria-hidden="true">
      <defs>
        <linearGradient id="sky" x1="0" y1="0" x2="0" y2="1">
          <stop offset="0" stop-color="var(--sky-top)"/>
          <stop offset="1" stop-color="var(--sky-bottom)"/>
        </linearGradient>
        <linearGradient id="flame" x1="0" y1="0" x2="0" y2="1">
          <stop offset="0" stop-color="var(--flame-top)"/>
          <stop offset="1" stop-color="var(--flame-bottom)"/>
        </linearGradient>
      </defs>
      <rect width="560" height="320" fill="url(#sky)"/>
      <path d="M262,0 C320,80 300,240 148,320 L140,320 C285,240 305,90 248,0 Z" fill="#4aa6f5" opacity="0.7"/>
      <path d="M262,0 C320,80 300,240 148,320 L560,320 L560,0 Z" fill="url(#flame)"/>
    </svg>

    <div class="contact">
      <p class="contact__name">Daniel Reeve</p>
      <p class="contact__title">Managing Director</p>

      <p class="contact__row">123.456.7890
        <svg class="contact__icon" viewBox="0 0 12 12"><path d="M2 1h2l1 3-1.3 1a7 7 0 0 0 3.3 3.3L8 7l3 1v2a1 1 0 0 1-1 1A9 9 0 0 1 1 2a1 1 0 0 1 1-1z" fill="#fff"/></svg>
      </p>
      <p class="contact__row">123.456.7890
        <svg class="contact__icon" viewBox="0 0 12 12"><rect x="3" y="1" width="6" height="4" fill="none" stroke="#fff"/><rect x="1" y="5" width="10" height="6" rx="1" fill="#fff"/></svg>
      </p>
      <p class="contact__row">info@youremail.com
        <svg class="contact__icon" viewBox="0 0 12 12"><rect x="1" y="2.5" width="10" height="7" fill="#fff"/><path d="M1 2.5l5 4 5-4" fill="none" stroke="#c9400c"/></svg>
      </p>
      <p class="contact__row">www.website.com
        <svg class="contact__icon" viewBox="0 0 12 12"><path d="M5 7l2-2M4.5 5L3 6.5a1.8 1.8 0 0 0 2.5 2.5L7 7.5M7.5 7L9 5.5A1.8 1.8 0 0 0 6.5 3L5 4.5" fill="none" stroke="#fff" stroke-width="1.3"/></svg>
      </p>

      <p class="contact__row contact__row--address">1234, Address Goes Here
        <svg class="contact__icon" viewBox="0 0 12 12"><path d="M6 11S2 6.8 2 4.5a4 4 0 0 1 8 0C10 6.8 6 11 6 11z" fill="#fff"/><circle cx="6" cy="4.5" r="1.4" fill="#c9400c"/></svg>
      </p>
      <p class="contact__row">Country Name, 123456
        <svg class="contact__icon contact__icon--blank" viewBox="0 0 12 12"></svg>
      </p>
    </div>
  </section>

</body>
</html>
```